Rollers & Glides.com

Vertical Business Card with focus on branding with our icon. Information on card will be logo, persons name, position, phone number, email address and website. Use the the name Marcus Pellow, position President, phone number 480.915.2267, email Marcus@rollersandglides-demo.com, website www.rollersandglides-demo.com.

```html
<!DOCTYPE html>
<html lang="en">
<head>
<meta charset="utf-8">
<title>Rollers &amp; Glides.com — Business Card</title>
<link href="https://fonts.googleapis.com/css2?family=Roboto:wght@400;700&family=Roboto+Condensed:wght@400&display=swap" rel="stylesheet">
<style>
  :root {
    --backdrop: #6b6b6b;
    --brand-blue: #3460ad;
    --card-dark: #1e1d1c;
    --ink-light: #ffffff;
    --rule: rgba(255,255,255,0.55);
    --shadow: rgba(0,0,0,0.55);
  }
  * { margin: 0; padding: 0; box-sizing: border-box; }
  html, body {
    width: 1093px; height: 1200px; overflow: hidden;
    background: var(--backdrop);
  }
  .canvas { position: relative; width: 1093px; height: 1200px; }

  .card {
    position: absolute; left: 265px; width: 578px; height: 357px;
    box-shadow: 3px 3px 3px var(--shadow);
  }
  .card--front { top: 226px; background: var(--brand-blue); color: var(--ink-light);
    font-family: "Roboto", Arial, sans-serif; text-align: center; }
  .card--back { top: 620px; background: var(--card-dark); }

  .person-name { position: absolute; top: 82px; width: 100%;
    font-weight: 700; font-size: 27px; letter-spacing: -0.5px; line-height: 1; }
  .person-role { position: absolute; top: 113px; width: 100%;
    font-weight: 400; font-size: 21px; line-height: 1; }

  .contact-icons { position: absolute; top: 153px; left: 0; width: 100%;
    display: flex; justify-content: center; align-items: center; gap: 5px; }
  .contact-icons .rule { width: 64px; height: 1px; background: var(--rule); margin: 0 5px; }
  .icon-tile { width: 31px; height: 31px; background: var(--ink-light);
    border-radius: 3px; display: flex; align-items: center; justify-content: center; }
  .icon-tile svg { width: 21px; height: 21px; }

  .contact-lines { position: absolute; top: 196px; width: 100%;
    font-size: 21px; line-height: 26.5px; }

  .wordmark { position: absolute; top: 0; left: 0; width: 100%; height: 100%;
    display: flex; align-items: center; justify-content: center; gap: 14px; }
  .wordmark-dot { width: 18px; height: 18px; border-radius: 50%; background: var(--brand-blue); }
  .wordmark-name { font-family: "Roboto Condensed", "Arial Narrow", sans-serif;
    font-weight: 400; font-size: 36px; color: var(--brand-blue); letter-spacing: 1px; }
</style>
</head>
<body>
<main class="canvas">
  <section class="card card--front" aria-label="Business card front">
    <h1 class="person-name">MARCUS PELLOW</h1>
    <p class="person-role">President</p>

    <div class="contact-icons">
      <span class="rule"></span>
      <span class="icon-tile" aria-label="Phone">
        <svg viewBox="0 0 24 24" fill="#3460ad">
          <path d="M3 8c0-3 5-4 9-4s9 1 9 4v1.5h-4V8c-1-.8-3-1-5-1s-4 .2-5 1v1.5H3z"/>
          <path d="M7 10h10l2 9H5z"/>
          <g fill="#fff"><circle cx="10" cy="13" r=".8"/><circle cx="12" cy="13" r=".8"/><circle cx="14" cy="13" r=".8"/><circle cx="10" cy="15.5" r=".8"/><circle cx="12" cy="15.5" r=".8"/><circle cx="14" cy="15.5" r=".8"/></g>
        </svg>
      </span>
      <span class="icon-tile" aria-label="Email">
        <svg viewBox="0 0 24 24" fill="none" stroke="#3460ad" stroke-width="1.6">
          <rect x="3" y="6" width="18" height="12"/>
          <path d="M3 6l9 7 9-7M3 18l7-6M21 18l-7-6"/>
        </svg>
      </span>
      <span class="icon-tile" aria-label="Website">
        <svg viewBox="0 0 24 24">
          <circle cx="12" cy="12" r="9" fill="#3460ad"/>
          <path d="M8 7c2-1 4 0 4 2s-2 2-2 4-2 1-3-1 0-4 1-5zM14 14c1-1 3-1 3 1s-1 3-3 3 -1-2 0-4z" fill="#fff"/>
        </svg>
      </span>
      <span class="rule"></span>
    </div>

    <address class="contact-lines" style="font-style:normal">
      <div class="contact-phone">480.915.2267</div>
      <div class="contact-email">Marcus@rollersandglides-demo.com</div>
      <div class="contact-web">www.rollersandglides-demo.com</div>
    </address>
  </section>

  <section class="card card--back" aria-label="Business card back">
    <div class="wordmark">
      <span class="wordmark-dot"></span>
      <span class="wordmark-name">Rollers &amp; Glides.com</span>
    </div>
  </section>
</main>
</body>
</html>
```